Create Social Media design templates for Online-Education-Startup

We are an online platform for pupils who provide group courses and on demand individual tutroing lessons. Our core values are personalisation, family and success. We need a holistic social media design concept which includes nine possible layouts for Instagram posts which reflect our values and promote not only our offerings and special deals but also support in building our brand image (for example: telling company history, daily news, funny facts, getting to know the team etc.).
Additionally, we need design elements for our YouTube channel:
-Videocover
-Cover Image for the channel

Our main colour is orange (RGB-Code: 255;105;31) and additional colours white, black, and grey. For the reference have a look at our website: www.lernvolta.de.

Target Market(s)

We want to attract customers to our online tutoring courses and build a brand.

Industry/Entity Type

Education / Tutoring

Font styles to use
Sans Serif

Requirements
Must have
• Familiarize yourself with the style of our website. The designs should fit as well as possible.

```html
<!DOCTYPE html>
<html lang="en">
<head>
<meta charset="utf-8">
<title>Lernvolta – Our Team post</title>
<link rel="stylesheet" href="https://fonts.googleapis.com/css2?family=Poppins:wght@300;400;500;600;700&display=swap">
<style>
  :root {
    --orange: #ff691f;
    --orange-band: #ee6a2d;
    --black: #0b0b0b;
    --white: #ffffff;
    --grey-text: #6b6b6b;
    --backdrop: #b3b3b3;
    --photo-light: #c9cbc6;
    --photo-dark: #7d8792;
  }
  html, body {
    margin: 0;
    padding: 0;
    width: 1200px;
    height: 796px;
    overflow: hidden;
    background: var(--backdrop);
    font-family: "Poppins", sans-serif;
  }
  .post {
    position: absolute;
    left: 222px;
    top: 20px;
    width: 756px;
    height: 756px;
    background: var(--white);
    overflow: hidden;
    box-shadow: 0 6px 18px rgba(0,0,0,0.25);
  }
  .post-shapes {
    position: absolute;
    inset: 0;
  }
  .brand {
    position: absolute;
    left: 145px;
    top: 30px;
    color: var(--black);
    line-height: 1.15;
  }
  .brand-name { font-size: 31px; font-weight: 700; display: block; }
  .brand-sub { font-size: 26px; font-weight: 400; display: block; }
  .web-address {
    position: absolute;
    right: 48px;
    top: 38px;
    font-size: 16.5px;
    color: var(--orange);
  }
  .band-heading {
    position: absolute;
    left: 36px;
    top: 188px;
    margin: 0;
    line-height: 1.15;
    font-size: 40px;
  }
  .band-heading .lead { color: var(--black); font-weight: 400; display: block; }
  .band-heading .name { color: var(--white); font-weight: 600; display: block; }
  .section-title {
    position: absolute;
    left: 36px;
    top: 378px;
    margin: 0;
    font-size: 74px;
    font-weight: 600;
    line-height: 0.86;
  }
  .section-title .accent { color: var(--orange); display: block; }
  .section-title .main { color: var(--black); display: block; }
  .intro {
    position: absolute;
    left: 48px;
    top: 549px;
    width: 330px;
    margin: 0;
    font-size: 18px;
    font-weight: 300;
    line-height: 27px;
    color: var(--grey-text);
  }
  .benefits {
    position: absolute;
    left: 478px;
    top: 510px;
    margin: 0;
    padding: 0;
    list-style: none;
  }
  .benefit {
    display: flex;
    align-items: center;
    height: 33px;
    margin-bottom: 15px;
    font-size: 21px;
    color: var(--black);
  }
  .benefit-icon {
    width: 33px;
    height: 33px;
    margin-right: 20px;
    flex: none;
  }
  .trial {
    position: absolute;
    left: 27px;
    top: 707px;
    font-size: 21px;
    font-weight: 600;
    color: var(--black);
  }
  .trial small { font-size: 15.5px; font-weight: 400; color: var(--white); }
  .contact {
    position: absolute;
    right: 66px;
    top: 680px;
    text-align: right;
    color: var(--white);
  }
  .contact-phone {
    display: flex;
    align-items: center;
    gap: 10px;
    font-size: 27px;
    font-weight: 500;
    line-height: 1.1;
  }
  .contact-phone svg { width: 22px; height: 22px; }
  .contact-mail { font-size: 13px; color: var(--orange); line-height: 1.2; }
</style>
</head>
<body>
  <article class="post">
    <svg class="post-shapes" width="756" height="756" viewBox="0 0 756 756">
      <defs>
        <linearGradient id="team-photo-tone" x1="0" y1="0" x2="0" y2="1">
          <stop offset="0" stop-color="var(--photo-light)"/>
          <stop offset="0.55" stop-color="#e6e7e4"/>
          <stop offset="1" stop-color="var(--photo-dark)"/>
        </linearGradient>
      </defs>
      <!-- orange title band -->
      <rect class="title-band" x="0" y="157" width="756" height="178" fill="var(--orange-band)"/>
      <!-- brand circle -->
      <circle class="brand-circle" cx="82" cy="73" r="46" fill="none" stroke="var(--orange)" stroke-width="6"/>
      <!-- team photo placeholder -->
      <g transform="rotate(-14 508 287)">
        <ellipse cx="508" cy="287" rx="214" ry="170" fill="var(--white)"/>
        <ellipse cx="508" cy="287" rx="202" ry="160" fill="url(#team-photo-tone)"
                 role="img" aria-label="Team photo: seven trainers in white shirts standing in front of a stone wall"/>
        <ellipse cx="508" cy="287" rx="222" ry="178" fill="none" stroke="var(--orange)" stroke-width="8"/>
      </g>
      <path class="ring-tail" d="M398 128 C450 122 500 124 555 116" fill="none" stroke="var(--orange)" stroke-width="8" stroke-linecap="round"/>
      <!-- title underline -->
      <rect class="title-rule" x="0" y="520" width="274" height="3" fill="var(--orange)"/>
      <!-- footer shapes -->
      <path class="footer-dark" d="M270 706 L420 706 C446 706 456 670 492 670 L756 670 L756 756 L270 756 Z" fill="var(--black)"/>
      <path class="footer-accent" d="M0 689 L255 689 C285 689 300 700 315 715 L356 756 L0 756 Z" fill="var(--orange)"/>
    </svg>

    <div class="brand">
      <span class="brand-name">Lernvolta</span>
      <span class="brand-sub">Bildungsinstitut</span>
    </div>
    <div class="web-address">www.lernvolta.de</div>

    <h1 class="band-heading">
      <span class="lead">We are</span>
      <span class="name">Lernvolta</span>
    </h1>

    <h2 class="section-title">
      <span class="accent">Our</span>
      <span class="main">Team</span>
    </h2>

    <p class="intro">The trainers at Lernvolta offer enthusiasm and professionalism. Our quality standards set us apart from other offers.</p>

    <ul class="benefits">
      <li class="benefit">
        <svg class="benefit-icon" viewBox="0 0 33 33">
          <rect width="33" height="33" rx="6" fill="var(--orange)"/>
          <circle cx="16.5" cy="16.5" r="9" fill="none" stroke="var(--white)" stroke-width="1.5"/>
          <path d="M16.5 11 V16.5 L20 19" fill="none" stroke="var(--white)" stroke-width="1.5" stroke-linecap="round"/>
        </svg>
        Time flexibility
      </li>
      <li class="benefit">
        <svg class="benefit-icon" viewBox="0 0 33 33">
          <rect width="33" height="33" rx="6" fill="var(--orange)"/>
          <circle cx="16.5" cy="16.5" r="8" fill="none" stroke="var(--white)" stroke-width="1.5" stroke-dasharray="3 2"/>
          <circle cx="16.5" cy="16.5" r="4" fill="none" stroke="var(--white)" stroke-width="1.5"/>
        </svg>
        Employee training
      </li>
      <li class="benefit">
        <svg class="benefit-icon" viewBox="0 0 33 33">
          <rect width="33" height="33" rx="6" fill="var(--orange)"/>
          <rect x="7" y="8" width="19" height="13" rx="1" fill="none" stroke="var(--white)" stroke-width="1.5"/>
          <path d="M13 25 H20 M16.5 21 V25" stroke="var(--white)" stroke-width="1.5"/>
        </svg>
        Online lessons
      </li>
    </ul>

    <div class="trial">Free Trial Lesson <small>Available!</small></div>

    <div class="contact">
      <div class="contact-phone">
        <svg viewBox="0 0 24 24"><path d="M6.6 3 L9.5 7.5 L7.6 9.6 C8.8 12 11.2 14.6 14.4 16.4 L16.5 14.5 L21 17.4 L19.3 20.6 C12 21 3.5 12.5 3.4 4.7 Z" fill="var(--white)"/></svg>
        030 55501234
      </div>
      <div class="contact-mail">kontakt@lernvolta.de</div>
    </div>
  </article>
</body>
</html>
```